Verlindo Magician

I want the business card for my business to give to people who watch that later I will be employed to show magic here is my website http://www.verlindoillusions.example/I want the interesting design , i am very opened for formal and informal, I watch a lot of design so don't stick to the common shape and form but i hope it can also be produced the thing to write on will be the same as in picture that i will upload , i also will upload the logo for you that so can be easy to useDenis CostilleMagicianMAGICIAN BALSAMO 17 rue des Tilleuls - 25000 BESANÇON contact@verlindoillusions.example tel. 0381 946 157 tel. 0674 219 503

```html
<!DOCTYPE html>
<html lang="fr">
<head>
<meta charset="utf-8">
<title>Verlindo Magicien – Business Card</title>
<link rel="stylesheet" href="https://fonts.googleapis.com/css2?family=Jost:wght@300;400&display=swap">
<style>
  :root {
    --stage: #3b3b3b;
    --card: #ffffff;
    --ink: #161616;
    --ink-soft: #444444;
    --accent: #e0202a;
    --art: #111111;
  }
  * { margin: 0; padding: 0; box-sizing: border-box; }
  html, body { width: 1200px; height: 960px; overflow: hidden; }
  body {
    background: var(--stage);
    font-family: "Jost", "Futura", sans-serif;
    color: var(--ink);
    position: relative;
  }
  .card {
    position: absolute;
    width: 620px;
    height: 354px;
    background: var(--card);
    overflow: hidden;
    box-shadow: 0 12px 30px rgba(0,0,0,0.45);
  }
  .card--back { left: 60px; top: 80px; }
  .card--front { left: 520px; top: 520px; }

  .portrait {
    position: absolute;
    background: var(--art);
    border-radius: 60px 60px 18px 18px;
  }
  .card--back .portrait { left: 240px; top: 58px; width: 140px; height: 130px; }
  .card--front .portrait {
    left: 34px; top: 70px; width: 280px; height: 284px;
    border-radius: 110px 110px 0 0;
  }

  .wordmark { font-weight: 300; line-height: 1; letter-spacing: 0.02em; }
  .wordmark__name { display: block; }
  .wordmark__sub { display: block; letter-spacing: 0.12em; }

  .card--back .wordmark {
    position: absolute; left: 0; right: 0; top: 200px; text-align: center;
  }
  .card--back .wordmark__name { font-size: 26px; }
  .card--back .wordmark__sub { font-size: 8px; margin-top: 3px; }

  .back-url {
    position: absolute; right: 40px; bottom: 34px;
    font-size: 14px; letter-spacing: 0.18em; color: var(--ink-soft); font-weight: 300;
  }

  .card--front .wordmark {
    position: absolute; right: 34px; top: 34px; text-align: right;
  }
  .card--front .wordmark__name { font-size: 48px; }
  .card--front .wordmark__sub { font-size: 11px; margin-top: 4px; }

  .identity { position: absolute; right: 44px; top: 120px; text-align: right; }
  .identity__name { font-size: 22px; font-weight: 400; }
  .identity__role { font-size: 15px; color: var(--accent); font-weight: 400; margin-top: -2px; }

  .contact {
    position: absolute; right: 24px; top: 186px; list-style: none; text-align: right;
    font-size: 13px; font-weight: 300; color: var(--ink-soft); line-height: 20px;
  }
  .contact__item { display: flex; justify-content: flex-end; align-items: center; gap: 8px; }
  .contact__icon { width: 12px; height: 12px; flex: none; }
  .contact__spacer { width: 12px; flex: none; }
</style>
</head>
<body>

  <section class="card card--back" aria-label="Card back">
    <div class="portrait" role="img" aria-label="Black and white illustration of the magician holding a playing card"></div>
    <div class="wordmark">
      <span class="wordmark__name">VERLINDO</span>
      <span class="wordmark__sub">MAGICIEN</span>
    </div>
    <p class="back-url">www.verlindoillusions.example</p>
  </section>

  <section class="card card--front" aria-label="Card front">
    <div class="portrait" role="img" aria-label="Large black and white illustration of the magician in a jacket holding a playing card"></div>
    <div class="wordmark">
      <span class="wordmark__name">VERLINDO</span>
      <span class="wordmark__sub">MAGICIEN</span>
    </div>
    <div class="identity">
      <p class="identity__name">Marc Ravoulet</p>
      <p class="identity__role">Magician</p>
    </div>
    <ul class="contact">
      <li class="contact__item">MAGICIAN VERLINDO<span class="contact__spacer"></span></li>
      <li class="contact__item">17 rue des Tilleuls - 25000 BESANÇON<span class="contact__spacer"></span></li>
      <li class="contact__item">0381 946 157
        <svg class="contact__icon" viewBox="0 0 12 12" aria-hidden="true"><path d="M2.5 1 L4.5 1 L5 3.5 L3.8 4.4 Q5 7 7.6 8.2 L8.5 7 L11 7.5 L11 9.5 Q10.5 11 9 11 Q1 10 1 3 Q1 1.5 2.5 1 Z" fill="#161616"/></svg>
      </li>
      <li class="contact__item">0674 219 503
        <svg class="contact__icon" viewBox="0 0 12 12" aria-hidden="true"><path d="M2.5 1 L4.5 1 L5 3.5 L3.8 4.4 Q5 7 7.6 8.2 L8.5 7 L11 7.5 L11 9.5 Q10.5 11 9 11 Q1 10 1 3 Q1 1.5 2.5 1 Z" fill="#161616"/></svg>
      </li>
      <li class="contact__item">contact@verlindoillusions.example
        <svg class="contact__icon" viewBox="0 0 12 12" aria-hidden="true"><rect x="0.5" y="2.5" width="11" height="7.5" fill="#161616"/><path d="M0.8 2.8 L6 7 L11.2 2.8" fill="none" stroke="#fff" stroke-width="1"/></svg>
      </li>
      <li class="contact__item">www.verlindoillusions.example
        <svg class="contact__icon" viewBox="0 0 12 12" aria-hidden="true"><circle cx="6" cy="6" r="5.5" fill="#161616"/><ellipse cx="6" cy="6" rx="2.3" ry="5.5" fill="none" stroke="#fff" stroke-width="0.8"/><line x1="0.5" y1="6" x2="11.5" y2="6" stroke="#fff" stroke-width="0.8"/></svg>
      </li>
    </ul>
  </section>

</body>
</html>
```